Business Card for Polygraph business in Africa

Business Card . Polygraph Examiner based in Tanzania, East Africa.
Business Card will be used to disseminate contact information to potential clients.
It should convey that I am a professional specifically in the polygraph field and perform my work with integrity.

I have attached the business card that I'm currently using, which I threw together myself initially. It's not professional enough.

Target Market(s)

Banks, Accounting Firms, Government Ministries, Gas, Oil, & Gemstone Mining Concerns, Wildlife Conservation NGOs, International companies located in East Africa.

Industry/Entity Type

Business

Contact Information for Business Card

Veritrace Kilonga
Miriam Holloway
PO Box 48317
Arusha, Tanzania
+255 612 839 274
miriamholloway@postvale.example

Colors
00a990
f37122
faa54b

Requirements
Must have
• - Veritrace Kilonga (with the word "Polygraph" being more prominent than the word "Tanzania")
• - Forensic Examinations
• - Employment Screening
• - Should contain a logo of the Continental Truthline Society (of which I'm a member)
• - I would like an accent design (such as the polygraph "squiggles" of a cardio tracing or such as that)
• - My contact information (less prominent, but large enough to read legibly). I would also consider putting the contact information on the second side of the card.
Nice to have
• My color suggestions are changeable.
Should not have
• Anything "cutesy" or "cartoonish"

```html
<!DOCTYPE html>
<html lang="en">
<head>
<meta charset="utf-8">
<title>Veritrace Kilonga – Business Card</title>
<link rel="stylesheet" href="https://fonts.googleapis.com/css2?family=Work+Sans:wght@400;600;700&family=Raleway:wght@400;500&display=swap">
<style>
  :root {
    --navy: #121b3d;
    --orange: #f37122;
    --white: #ffffff;
    --paper-bg: #e4e4e6;
    --seal-blue: #2a2f8f;
  }
  * { box-sizing: border-box; margin: 0; padding: 0; }
  html, body { width: 1200px; height: 900px; overflow: hidden; }
  body {
    background: var(--paper-bg);
    position: relative;
    font-family: "Raleway", sans-serif;
  }
  .card {
    position: absolute;
    left: 250px;
    width: 700px;
    height: 400px;
    overflow: hidden;
    box-shadow: 0 6px 18px rgba(0,0,0,0.18);
  }
  /* Back side */
  .card--back {
    top: 40px;
    background: var(--navy);
    display: flex;
    align-items: center;
    justify-content: center;
  }
  .card--back .brand-name {
    color: var(--white);
    font-family: "Work Sans", sans-serif;
    font-weight: 700;
    font-size: 40px;
    letter-spacing: 0.5px;
  }
  /* Front side */
  .card--front {
    top: 470px;
    background: var(--white);
  }
  .front-header {
    position: absolute;
    left: 0; top: 0;
    width: 100%;
    height: 205px;
  }
  .front-header .brand-name {
    position: absolute;
    left: 56px;
    top: 82px;
    color: var(--navy);
    font-family: "Work Sans", sans-serif;
    font-weight: 700;
    font-size: 30px;
  }
  .member-seal {
    position: absolute;
    right: 60px;
    top: 40px;
    width: 135px;
    height: 135px;
  }
  .accent-rule {
    position: absolute;
    left: 0; top: 205px;
    width: 100%;
    height: 3px;
    background: var(--orange);
  }
  .front-footer {
    position: absolute;
    left: 0; top: 214px;
    width: 100%;
    height: 186px;
    background: var(--navy);
  }
  .contact {
    position: absolute;
    left: 56px;
    top: 18px;
    color: var(--white);
  }
  .contact .person-name {
    color: var(--orange);
    font-family: "Raleway", sans-serif;
    font-weight: 500;
    font-size: 28px;
    letter-spacing: 2px;
    text-transform: uppercase;
    margin-bottom: 8px;
  }
  .contact .line {
    font-size: 17px;
    line-height: 24px;
    letter-spacing: 0.4px;
    display: flex;
    align-items: center;
    gap: 10px;
  }
  .contact .line--plain { padding-left: 0; }
  .contact .icon { width: 14px; height: 14px; flex: none; }
  .services {
    position: absolute;
    right: 56px;
    bottom: 26px;
    text-align: right;
    color: var(--white);
    font-family: "Work Sans", sans-serif;
    font-weight: 600;
    font-size: 15px;
    letter-spacing: 2px;
    line-height: 26px;
    text-transform: uppercase;
  }
</style>
</head>
<body>

  <section class="card card--back">
    <span class="brand-name">Veritrace Kilonga</span>
  </section>

  <section class="card card--front">
    <div class="front-header">
      <span class="brand-name">Veritrace Kilonga</span>
      <svg class="member-seal" viewBox="0 0 135 135" role="img" aria-label="Continental Truthline Society membership seal">
        <circle cx="67.5" cy="67.5" r="64" fill="var(--seal-blue)"/>
        <circle cx="67.5" cy="67.5" r="52" fill="var(--white)"/>
        <circle cx="67.5" cy="67.5" r="34" fill="#c9cbe6"/>
      </svg>
    </div>
    <div class="accent-rule"></div>
    <div class="front-footer">
      <div class="contact">
        <div class="person-name">Miriam Holloway</div>
        <div class="line line--plain">PO Box 48317</div>
        <div class="line line--plain">Arusha, Tanzania</div>
        <div class="line">
          <svg class="icon" viewBox="0 0 16 16" aria-hidden="true">
            <path d="M4 1.5l2.5 3-1.6 1.8c.8 1.9 2.2 3.4 4.2 4.3l1.7-1.6 3 2.4-1.3 2.4C7.6 13.6 2.4 8.4 2 2.8z" fill="var(--orange)"/>
          </svg>
          <span>+255 612 839 274</span>
        </div>
        <div class="line">
          <svg class="icon" viewBox="0 0 16 16" aria-hidden="true">
            <rect x="1.5" y="3.5" width="13" height="9" fill="none" stroke="var(--orange)" stroke-width="1.5"/>
            <path d="M1.5 3.5L8 9l6.5-5.5" fill="none" stroke="var(--orange)" stroke-width="1.5"/>
          </svg>
          <span>miriamholloway@postvale.example</span>
        </div>
      </div>
      <div class="services">
        <div>Issue Investigation</div>
        <div>Employment Screening</div>
      </div>
    </div>
  </section>

</body>
</html>
```